Willow Cradle Pregnancy and Baby Massage

I need a web design for a new business, WILLOW CRADLE PREGNANCY AND BABY MASSAGE that I am in the process of setting up in the suburbs of Perth, Western Australia. The business is owned and operated by myself and my intention is to service Pregnant Mothers and Parents of Young Babies that would benefit from massage. I would like to have a "Home Page" and pages for "About Me", "Pregnancy Massage", "Baby Massage", a Pricing Page for Pregnancy Massage Sessions, a Pricing Page for Baby Massage Sessions, and a "Contact Me" page to allow clients to either contact me with queries or book available pregnancy massage sessions on a particular day of the week. I would also like a "News" page that would include articles I have written, news about new courses and a link to my Facebook page (yet to be set up). I would like to keep the colour schemes similar to my logo design colours. I need the design to be easy to follow and to appeal to a younger audience (20's to mid 30's).
The target audience is pregnant mothers-to-be wishing to receive massage treatments, and new parents and grandparents of small babies that would like to learn how to massage their babies.
The look and feel should be modern, professional, elegant and feminine.
I need the design to be in a standard format such that I can update the content by myself ( and does not need specialised software) as the company and business progresses.

Target Market(s)

Contact Information for Business Card

Card should have rounded edges. Design should have the same "feel" as the website. Contact Details of my business address, mobile phone, email and website should be included.

Font styles to use
Script

Requirements
Must have
• Same colours as logo design. In cmyk system, the colours are: 20,60,0,0 which best result is pantone 681 and 40,40,0,0 which best result is pantone 2645. Card should include the logo design.

```html
<!DOCTYPE html>
<html lang="en">
<head>
<meta charset="utf-8">
<title>Willow Cradle Pregnancy and Baby Massage</title>
<link rel="stylesheet" href="https://fonts.googleapis.com/css2?family=Poppins:wght@300;400;500&family=Allura&display=swap">
<style>
:root{
  --plum:#b2649e;
  --lavender:#8b80b8;
  --lilac:#9088be;
  --ink:#3a3a3a;
  --white:#ffffff;
  --night:#000000;
  --rule:#2a2a2a;
  --soft-text:#d8d8d8;
}
*{margin:0;padding:0;box-sizing:border-box}
html,body{width:1200px;height:2582px;overflow:hidden;background:var(--white)}
body{position:relative;font-family:"Poppins",sans-serif;color:var(--ink)}
.abs{position:absolute}

/* header */
.brand{left:86px;top:30px;display:flex;align-items:center;gap:14px}
.brand-dot{width:54px;height:54px;border-radius:50%;background:var(--plum)}
.brand-name{font-family:"Poppins",sans-serif;font-weight:500;font-size:21px;line-height:1.25;color:var(--plum);width:200px}
.header-phone{left:738px;top:38px;display:flex;align-items:center;gap:12px;font-size:24px;color:var(--lavender);font-weight:300}
.social{display:flex;gap:8px}
.social span{display:block;width:31px;height:31px;border-radius:50%;background:var(--lavender)}
.header-social{left:962px;top:36px}
.nav{left:448px;top:82px;display:flex;gap:0;font-size:14px;color:var(--ink)}
.nav a{color:inherit;text-decoration:none;padding:0 13px;line-height:34px;position:relative}
.nav a.active{background:var(--plum);color:var(--white)}
.nav a.active::after{content:"";position:absolute;left:50%;bottom:-6px;margin-left:-6px;border:6px solid transparent;border-bottom:0;border-top-color:var(--plum)}
.top-rule{left:0;top:151px;width:1200px;height:4px;background:var(--lavender)}

/* hero */
.hero{left:0;top:155px;width:1200px;height:610px}
.hero-title{left:86px;top:335px;width:460px;text-align:center;color:var(--white)}
.hero-welcome{font-size:41px;font-weight:300;letter-spacing:1px;margin-left:-46px}
.hero-name{font-family:"Allura",cursive;font-size:108px;line-height:1;margin-top:4px;margin-left:-20px}
.hero-sub{font-size:18px;letter-spacing:.5px;text-align:right;margin-top:8px;margin-right:-4px}

.intro{left:180px;top:818px;width:840px;text-align:center;font-size:22px;line-height:33px;color:var(--lavender);font-weight:300}

.feature{left:0;top:970px;width:1200px;height:610px}

.vision{left:160px;top:1628px;width:880px;text-align:center;font-size:22px;line-height:32px;color:var(--lavender);font-weight:300}
.vision p+p{margin-top:32px}

/* footer */
.footer-band{left:0;top:2060px;width:1200px;height:522px}
.badge{left:444px;top:1946px;width:311px;height:181px;background:var(--white);border:1px solid #d6d6d6;box-shadow:0 2px 6px rgba(0,0,0,.25)}
.badge-shape{position:absolute;left:24px;top:22px;width:262px;height:136px;background:linear-gradient(90deg,#e9dbea,#f3eef6)}
.col{top:2160px;color:var(--white)}
.col h3{font-size:17px;font-weight:500;letter-spacing:.5px;padding-bottom:16px;border-bottom:1px solid #444;width:241px}
.col-contact{left:86px}
.col-news{left:472px}
.col-links{left:864px}
.contact-list{list-style:none;margin-top:24px;font-size:13.5px;line-height:22px}
.contact-list li{display:flex;gap:18px;margin-bottom:16px}
.contact-list svg{flex:none;margin-top:4px}
.footer-social{margin-top:2px}
.footer-social span{width:30px;height:30px}
.news-text{margin-top:26px;font-size:13px;line-height:22px;padding-left:4px}
.email-field{margin-top:22px;margin-left:4px;width:253px;height:41px;background:var(--white);color:#888;font-size:11px;line-height:41px;padding-left:20px}
.submit{margin-left:4px;margin-top:14px;width:253px;height:41px;background:var(--lilac);color:var(--white);font-size:17px;font-weight:500;letter-spacing:1px;text-align:center;line-height:41px}
.links{list-style:none;margin-top:24px;font-size:13px;line-height:31px}
.bottom-rule{left:86px;top:2483px;width:1027px;height:1px;background:#333}
.copyright{left:0;top:2512px;width:1200px;text-align:center;font-size:13.5px;color:var(--soft-text)}
</style>
</head>
<body>

<header>
  <div class="abs brand"><span class="brand-dot"></span><span class="brand-name">Willow Cradle Pregnancy and Baby Massage</span></div>
  <div class="abs header-phone">
    <svg width="18" height="18" viewBox="0 0 24 24" fill="#8b80b8"><path d="M6.6 10.8a15 15 0 0 0 6.6 6.6l2.2-2.2a1 1 0 0 1 1-.25 11.4 11.4 0 0 0 3.6.57 1 1 0 0 1 1 1V20a1 1 0 0 1-1 1A17 17 0 0 1 3 4a1 1 0 0 1 1-1h3.5a1 1 0 0 1 1 1c0 1.25.2 2.45.57 3.6a1 1 0 0 1-.25 1z"/></svg>
    +0123 555 014
  </div>
  <div class="abs social header-social"><span></span><span></span><span></span><span></span></div>
  <nav class="abs nav">
    <a class="active">Home</a><a>About Me</a><a>Pregnancy Massage</a><a>Baby Massage</a><a>Pricing</a><a>News</a><a>Contact Me</a>
  </nav>
  <div class="abs top-rule"></div>
</header>

<svg class="abs hero" viewBox="0 0 1200 610" role="img" aria-label="Photograph of two sleeping newborn twins wrapped in a coral blanket inside a lace heart">
  <defs>
    <linearGradient id="heroFill" x1="0" y1="0" x2="1" y2="1">
      <stop offset="0" stop-color="#8a6a72"/>
      <stop offset=".5" stop-color="#a27b7c"/>
      <stop offset="1" stop-color="#c8907e"/>
    </linearGradient>
    <filter id="edgeShade"><feDropShadow dx="0" dy="4" stdDeviation="5" flood-opacity=".3"/></filter>
  </defs>
  <path d="M0 0H1200V575Q600 625 0 575Z" fill="url(#heroFill)" filter="url(#edgeShade)"/>
</svg>
<div class="abs hero-title">
  <div class="hero-welcome">WELCOME TO</div>
  <div class="hero-name">Willow Cradle</div>
  <div class="hero-sub">PREGNANCY &amp; BABY MASSAGE</div>
</div>

<p class="abs intro">Willow Cradle Pregnancy and Baby Massage was launched in 2017, offering massage for pregnant women, and instruction of baby massage to parents, grandparents and carers.</p>

<svg class="abs feature" viewBox="0 0 1200 610" role="img" aria-label="Photograph of newborn twins asleep in a round woven basket lined with soft fur">
  <defs>
    <radialGradient id="featureFill" cx=".5" cy=".5" r=".6">
      <stop offset="0" stop-color="#8a6a5c"/>
      <stop offset=".45" stop-color="#b18d6f"/>
      <stop offset="1" stop-color="#d8b58e"/>
    </radialGradient>
    <filter id="featureShade"><feDropShadow dx="0" dy="0" stdDeviation="6" flood-opacity=".3"/></filter>
  </defs>
  <path d="M0 5Q600 40 1200 5V590Q600 620 0 590Z" fill="url(#featureFill)" filter="url(#featureShade)"/>
</svg>

<div class="abs vision">
  <p>My vision is to provide a professional massage service to pregnant mothers and babies that also benefits from my skills and experience as a midwife.</p>
  <p>My expectation is that after each session, my clients should leave feeling relaxed, calm, emotionally nurtured, soothed and supported.</p>
  <p>At all times, I will take the utmost care of your privacy, safety and comfort in what is a very personal, intimate time in your life.</p>
</div>

<svg class="abs footer-band" viewBox="0 0 1200 522">
  <path d="M0 6Q600 40 1200 6V522H0Z" fill="#8b80b8"/>
  <path d="M0 16Q600 50 1200 16V522H0Z" fill="#000"/>
</svg>
<div class="abs badge"><div class="badge-shape"></div></div>

<footer>
  <section class="abs col col-contact">
    <h3>GET IN TOUCH</h3>
    <ul class="contact-list">
      <li><svg width="10" height="14" viewBox="0 0 10 14" fill="#fff"><path d="M5 0a5 5 0 0 0-5 5c0 3.6 5 9 5 9s5-5.4 5-9a5 5 0 0 0-5-5zm0 7a2 2 0 1 1 0-4 2 2 0 0 1 0 4z"/></svg><span>27 Banksia Grove, Kelmscott,<br>WA, Western Australia, 6111.</span></li>
      <li><svg width="11" height="11" viewBox="0 0 24 24" fill="#fff"><path d="M6.6 10.8a15 15 0 0 0 6.6 6.6l2.2-2.2a1 1 0 0 1 1-.25 11.4 11.4 0 0 0 3.6.57 1 1 0 0 1 1 1V20a1 1 0 0 1-1 1A17 17 0 0 1 3 4a1 1 0 0 1 1-1h3.5a1 1 0 0 1 1 1c0 1.25.2 2.45.57 3.6a1 1 0 0 1-.25 1z"/></svg><span>+0123 555 014</span></li>
      <li><svg width="12" height="10" viewBox="0 0 12 10" fill="#fff"><path d="M0 0h12v1.5L6 5 0 1.5zM0 3l6 3.5L12 3v7H0z"/></svg><span>hello@willowcradle.example</span></li>
    </ul>
    <div class="social footer-social"><span></span><span></span><span></span><span></span><span></span></div>
  </section>

  <section class="abs col col-news">
    <h3>NEWSLETTER SIGN UP</h3>
    <p class="news-text">Don't miss our news and updates.<br>Subscribe now!</p>
    <div class="email-field">Enter Email</div>
    <div class="submit">SUBMIT</div>
  </section>

  <section class="abs col col-links">
    <h3>QUICK LINK</h3>
    <ul class="links">
      <li>&gt; Home</li><li>&gt; About Me</li><li>&gt; Pregnancy Massage</li><li>&gt; Baby Massage</li><li>&gt; Pricing</li><li>&gt; News</li><li>&gt; Contact Me</li>
    </ul>
  </section>

  <div class="abs bottom-rule"></div>
  <p class="abs copyright">Copyright © 2017. Willow Cradle Pregnancy &amp; Baby Massage. All rights reserved</p>
</footer>

</body>
</html>
```